Landing Page and Logo for Auto-Blogging Platform

I created a platform that allows users to start a blog for their business, hobby, charity, etc. I need a landing page where users can learn about the platform, benefits of consistent blogging, SEO value, plans/pricing, etc. The landing page needs to have multiple call to action buttons encouraging the visitor to register/sign up for a free trial.

In addition to the landing page, I need a page for users to establish the settings for their blog. This page should be a fairly simple form, intended for the user to enter a few details to set up their blog:
1. Name of Blog
2. Up to 10 topics and/or keywords the blog should focus on
3. Theme: Color-scheme and logo upload for blog.

I have attached the specifications of the platform's functionality so you can better understand how it works, plans/pricing, etc.

I also need a logo for the business. The name of the platform is PostNook.

Target Market(s)

Website owners, bloggers, business owners

Industry/Entity Type

Technology, Internet, web design

Coding

Coded - Design and coding required

Number of Pages Required

2 page

Colors
0054AA
0677BA
7BADD7
CADEEF
E8F1F8
0094D4
00A9DD
6FCCEA
C7EBF8
E9F6FB

Requirements
Must have
• Eye-catching design but fairly light on content (keep it simple and brief.)
Nice to have
• Eye-catching yet simple design, clean and easy to understand what we are offering.
Should not have
• Too much “wordy” and confusing content.

```html
<!DOCTYPE html>
<html lang="en">
<head>
<meta charset="UTF-8">
<title>PostNook – Turning Thoughts Into Conversations</title>
<link href="https://fonts.googleapis.com/css2?family=Poppins:wght@400;500;600;700&display=swap" rel="stylesheet">
<style>
:root{
  --blue-deep:#0054AA;
  --blue-mid:#0677BA;
  --blue-bright:#0094D4;
  --blue-accent:#1A9BDC;
  --blue-soft:#CADEEF;
  --blue-pale:#E8F1F8;
  --sky-pale:#E9F6FB;
  --ink:#1E1E1E;
  --text:#333333;
  --dark:#2F2F2F;
  --footer:#262626;
  --white:#FFFFFF;
  --star:#F5B82E;
}
*{margin:0;padding:0;box-sizing:border-box}
html,body{width:1200px;height:4648px;overflow:hidden}
body{font-family:'Poppins',sans-serif;color:var(--text);background:var(--white)}
section,header,footer{position:relative;width:1200px}
.abs{position:absolute}
.hl{color:var(--blue-accent)}
.btn{position:absolute;display:flex;align-items:center;justify-content:center;font-size:13px;font-weight:500;text-decoration:none}
.btn-solid{background:var(--blue-deep);color:var(--white)}
.btn-light{background:var(--white);color:var(--ink)}
.bar{position:absolute;height:3px;width:52px;background:var(--blue-bright)}
.section-title{position:absolute;font-size:28px;font-weight:700;line-height:36px;color:var(--ink);text-transform:uppercase}
.illus{position:absolute;border-radius:24px}

/* header */
.site-header{height:80px;box-shadow:0 2px 10px rgba(0,0,0,.04)}
.brand{left:141px;top:24px;display:flex;align-items:center;gap:8px;font-size:18px;font-weight:700;color:var(--blue-deep);letter-spacing:.5px}
.brand-dot{width:14px;height:14px;border-radius:50%;background:var(--blue-deep)}
.header-cta{left:971px;top:22px;width:87px;height:36px;background:var(--blue-bright);color:var(--white);border-radius:4px;font-size:12px}

/* hero */
.hero{height:1039px}
.hero-title{top:60px;width:100%;text-align:center;font-size:47px;font-weight:600;line-height:56px;color:var(--ink)}
.hero-sub{top:125px;width:100%;text-align:center;font-size:16px;line-height:27px;color:var(--text)}
.hero-cta{left:511px;top:203px;width:177px;height:40px;background:var(--blue-bright);color:var(--white);border-radius:4px}
.avatars{left:496px;top:275px;display:flex}
.avatars span{width:26px;height:26px;border-radius:50%;border:2px solid var(--white);margin-left:-3px}
.join{top:312px;width:100%;text-align:center;font-size:12px;line-height:21px;color:var(--text)}
.join b{color:var(--blue-bright);font-weight:500}
.hero-art{left:162px;top:386px;width:885px;height:617px;border-radius:300px 300px 40px 40px;background:radial-gradient(ellipse at 50% 40%,#DCE6F7 0%,#EEF3FB 55%,#F8FAFD 100%)}

/* about */
.about{height:551px}
.about-art{left:141px;top:27px;width:419px;height:434px;background:linear-gradient(160deg,#F4F8FC,#E6F0F9 60%,#FDF1DD)}
.about-title{left:644px;top:69px}
.about .bar{left:644px;top:110px}
.about-copy{left:644px;top:153px;width:400px;font-size:12px;line-height:19px;color:var(--text)}
.about-cta{left:644px;top:379px;width:212px;height:42px}

/* how it works */
.how{height:765px;background:var(--blue-deep);color:var(--white)}
.how-title{top:78px;width:100%;text-align:center;color:var(--white)}
.how .bar{left:574px;top:120px;background:var(--blue-bright)}
.how-copy{left:316px;top:162px;width:569px;text-align:center;font-size:12px;line-height:19px}
.step{position:absolute;width:220px;text-align:center}
.step-icon{width:92px;height:92px;margin:0 auto;border-radius:50%;background:var(--white);display:flex;align-items:center;justify-content:center}
.step-label{margin-top:15px;font-size:19px;font-weight:600;line-height:28px}
.how-cta{left:495px;top:639px;width:211px;height:40px}

/* lists */
.ticks{position:absolute;list-style:none}
.ticks li{height:34px;display:flex;align-items:center;gap:12px;font-size:12px;font-weight:500;color:var(--text)}

/* benefits */
.benefits{height:567px}
.benefits-title{left:141px;top:92px}
.benefits .col-a{left:141px;top:210px}
.benefits .col-b{left:354px;top:210px}
.benefits-cta{left:141px;top:437px;width:211px;height:39px}
.benefits-art{left:641px;top:83px;width:415px;height:406px;background:linear-gradient(180deg,#FFFFFF,#EDF4FB 55%,#FCEFD8)}

/* seo */
.seo{height:554px;background:var(--sky-pale)}
.seo-art{left:141px;top:66px;width:419px;height:398px;background:linear-gradient(160deg,#F6FAFD,#DCEBF7 60%,#FBEBCC)}
.seo-title{left:642px;top:114px}
.seo .bar{left:642px;top:151px}
.seo .col-a{left:642px;top:193px}
.seo .col-b{left:859px;top:193px}
.seo-cta{left:642px;top:388px;width:210px;height:39px}

/* pricing */
.pricing{height:601px;background:var(--dark);color:var(--white)}
.pricing-title{top:70px;width:100%;text-align:center;color:var(--white)}
.pricing .bar{left:574px;top:114px;background:var(--blue-bright)}
.pricing-copy{left:285px;top:153px;width:630px;text-align:center;font-size:12px;line-height:19px}
.plans{left:271px;top:229px;width:659px;display:grid;grid-template-columns:repeat(3,1fr);background:var(--sky-pale)}
.plan{text-align:center;border-right:1px solid #C9DDEB}
.plan:last-child{border-right:none}
.plan h3{height:42px;line-height:42px;background:var(--blue-deep);color:var(--white);font-size:17px;font-weight:600;border-right:1px solid #3F7EC4}
.plan:last-child h3{border-right:none}
.plan p{padding:20px 14px 0;height:157px;font-size:12px;line-height:19px;color:var(--text)}
.price{display:block;margin-top:6px;font-size:22px;font-weight:600;color:var(--blue-bright)}
.price small{font-size:12px;font-weight:500}
.pricing-cta{left:495px;top:473px;width:211px;height:40px}

/* testimonials */
.reviews{height:455px}
.reviews-title{top:77px;width:100%;text-align:center}
.card{position:absolute;top:148px;width:290px;height:220px;background:var(--sky-pale);border-radius:12px;padding:28px 26px}
.stars{color:var(--star);font-size:14px;letter-spacing:3px}
.card p{margin-top:10px;font-size:12px;line-height:19px;color:var(--text)}
.author{position:absolute;left:26px;bottom:30px;display:flex;align-items:center;gap:14px;font-size:13px;font-weight:500;color:var(--ink)}
.author span{width:38px;height:38px;border-radius:50%}
.quote{position:absolute;right:26px;bottom:6px;font-size:80px;line-height:80px;font-weight:700;color:#7BC3E8;font-family:Georgia,serif}
.arrow{position:absolute;top:241px;width:34px;height:34px;border-radius:50%;display:flex;align-items:center;justify-content:center}
.arrow-prev{left:75px;background:var(--blue-pale)}
.arrow-next{left:1089px;background:var(--blue-deep)}

.site-footer{height:36px;background:var(--footer);color:#DDDDDD;font-size:11px;display:flex;align-items:center;justify-content:center}
</style>
</head>
<body>
<svg width="0" height="0" style="position:absolute">
  <symbol id="tick" viewBox="0 0 14 14"><circle cx="7" cy="7" r="6" fill="none" stroke="#0094D4" stroke-width="1.3"/><path d="M4.2 7.2l2 2 3.8-4" fill="none" stroke="#0094D4" stroke-width="1.4" stroke-linecap="round" stroke-linejoin="round"/></symbol>
</svg>

<header class="site-header">
  <div class="abs brand"><span class="brand-dot"></span>POSTNOOK</div>
  <a class="btn header-cta" href="#">Sign Up</a>
</header>

<section class="hero">
  <h1 class="abs hero-title">Turning <span class="hl">Thoughts</span> Into <span class="hl">Conversations.</span></h1>
  <p class="abs hero-sub">Write your content on Notely and automatically publish it to your SEO-friendly blog<br>– No coding or design skills required.</p>
  <a class="btn hero-cta" href="#">Start Your Free Trial</a>
  <div class="abs avatars" role="img" aria-label="Row of community member avatars">
    <span style="background:#E7B7A4"></span><span style="background:#C98F6E"></span><span style="background:#9FB6D6"></span><span style="background:#B77C5B"></span><span style="background:#E2C08A"></span><span style="background:#A9C4E0"></span><span style="background:#F0B56A"></span><span style="background:#D9A48C"></span><span style="background:#EFC3A0"></span>
  </div>
  <p class="abs join">Join <b>175+ creators, and new-age startups</b><br>and start publishing your content today</p>
  <div class="illus hero-art" role="img" aria-label="Illustration of a team building and publishing blog content around a large browser window"></div>
</section>

<section class="about">
  <div class="illus about-art" role="img" aria-label="Illustration of a person at a laptop designing a web page layout"></div>
  <h2 class="section-title about-title">About the <span class="hl">Platform</span></h2>
  <span class="bar"></span>
  <p class="abs about-copy">Lorem Ipsum is simply dummy text of the printing and typesetting industry. Lorem Ipsum has been the industry's standard dummy text ever since the 1500s, when an unknown printer took a galley of type and scrambled it to make a type specimen book. It has survived not only five centuries, but also the leap into electronic typesetting, remaining essentially unchanged. It was popularised in the 1960s with the release of Typeset sheets containing Lorem Ipsum passages, and more recently with desktop publishing software like Quill PageForge including versions of Lorem Ipsum.</p>
  <a class="btn btn-solid about-cta" href="#">Sign Up For A Free Trial</a>
</section>

<section class="how">
  <h2 class="section-title how-title">How it work</h2>
  <span class="bar"></span>
  <p class="abs how-copy">The purpose of this platform is to allow anyone to start a blog and automate the process of creating content and posting it to the blog. Here is what the platform will consist of.</p>

  <div class="step" style="left:78px;top:240px"><div class="step-icon"><svg width="44" height="44" viewBox="0 0 44 44" fill="none" stroke="#0677BA" stroke-width="2"><circle cx="22" cy="18" r="12"/><circle cx="22" cy="15" r="4"/><path d="M15 25c2-4 12-4 14 0"/><rect x="12" y="33" width="20" height="6" rx="3"/></svg></div><div class="step-label">Log in</div></div>
  <div class="step" style="left:329px;top:240px"><div class="step-icon"><svg width="44" height="44" viewBox="0 0 44 44" fill="none" stroke="#0677BA" stroke-width="2"><rect x="8" y="10" width="24" height="20" rx="2"/><path d="M4 34h32l-3-4H7z"/><path d="M18 24l14-14 3 3-14 14h-3z"/></svg></div><div class="step-label">Create a new<br>blog post</div></div>
  <div class="step" style="left:614px;top:240px"><div class="step-icon"><svg width="44" height="44" viewBox="0 0 44 44" fill="none" stroke="#0677BA" stroke-width="2"><rect x="8" y="6" width="28" height="32" rx="2"/><rect x="12" y="10" width="9" height="9"/><path d="M24 12h8M24 16h8M12 24h20M12 28h20M12 32h14"/></svg></div><div class="step-label">Format and<br>optimize</div></div>
  <div class="step" style="left:901px;top:240px"><div class="step-icon"><svg width="44" height="44" viewBox="0 0 44 44" fill="none" stroke="#0677BA" stroke-width="2"><rect x="5" y="9" width="34" height="26" rx="2"/><path d="M5 15h34"/><path d="M12 30l22-10-8 12-4-4z"/></svg></div><div class="step-label">Publish or<br>schedule</div></div>
  <div class="step" style="left:200px;top:438px"><div class="step-icon"><svg width="44" height="44" viewBox="0 0 44 44" fill="none" stroke="#0677BA" stroke-width="2"><rect x="6" y="8" width="20" height="14" rx="2"/><rect x="18" y="20" width="20" height="14" rx="2"/><path d="M10 22v5l5-5M34 34v4l-4-4"/></svg></div><div class="step-label">Engage with<br>readers</div></div>
  <div class="step" style="left:487px;top:438px"><div class="step-icon"><svg width="44" height="44" viewBox="0 0 44 44" fill="none" stroke="#0677BA" stroke-width="2"><rect x="6" y="8" width="32" height="22" rx="2"/><path d="M16 36h12M22 30v6"/><path d="M11 24l6-6 5 4 9-9"/></svg></div><div class="step-label">Monitor<br>performance</div></div>
  <div class="step" style="left:773px;top:438px"><div class="step-icon"><svg width="44" height="44" viewBox="0 0 44 44" fill="none" stroke="#0677BA" stroke-width="2"><circle cx="22" cy="22" r="13"/><circle cx="22" cy="22" r="5"/><path d="M22 5v4M22 35v4M5 22h4M35 22h4M10 10l3 3M31 31l3 3M34 10l-3 3M13 31l-3 3"/></svg></div><div class="step-label">Adjust and<br>improve</div></div>

  <a class="btn btn-light how-cta" href="#">Sign Up For A Free Trial</a>
</section>

<section class="benefits">
  <h2 class="section-title benefits-title">Benefits of <span class="hl">Consistent</span><br><span class="hl">Blogging</span></h2>
  <ul class="ticks col-a">
    <li><svg width="14" height="14"><use href="#tick"/></svg>Improved SEO</li>
    <li><svg width="14" height="14"><use href="#tick"/></svg>Increased Authority</li>
    <li><svg width="14" height="14"><use href="#tick"/></svg>Enhanced Engagement</li>
    <li><svg width="14" height="14"><use href="#tick"/></svg>Content Variety</li>
    <li><svg width="14" height="14"><use href="#tick"/></svg>Higher Conversion Rates</li>
  </ul>
  <ul class="ticks col-b">
    <li><svg width="14" height="14"><use href="#tick"/></svg>Brand Visibility</li>
    <li><svg width="14" height="14"><use href="#tick"/></svg>Audience Insights</li>
    <li><svg width="14" height="14"><use href="#tick"/></svg>Enhanced Social Media Presence</li>
    <li><svg width="14" height="14"><use href="#tick"/></svg>Networking Opportunities</li>
    <li><svg width="14" height="14"><use href="#tick"/></svg>Long-Term Benefits</li>
  </ul>
  <a class="btn btn-solid benefits-cta" href="#">Sign Up For A Free Trial</a>
  <div class="illus benefits-art" role="img" aria-label="Illustration of a person climbing rising bar chart steps toward a goal"></div>
</section>

<section class="seo">
  <div class="illus seo-art" role="img" aria-label="Illustration of a person with a tablet in front of a large SEO search screen and rocket"></div>
  <h2 class="section-title seo-title">SEO <span class="hl">Value</span></h2>
  <span class="bar"></span>
  <ul class="ticks col-a">
    <li><svg width="14" height="14"><use href="#tick"/></svg>Fresh Content</li>
    <li><svg width="14" height="14"><use href="#tick"/></svg>Keyword Optimization</li>
    <li><svg width="14" height="14"><use href="#tick"/></svg>Increased Indexing</li>
    <li><svg width="14" height="14"><use href="#tick"/></svg>Internal Linking</li>
    <li><svg width="14" height="14"><use href="#tick"/></svg>Backlink Opportunities</li>
  </ul>
  <ul class="ticks col-b">
    <li><svg width="14" height="14"><use href="#tick"/></svg>Engagement Metrics</li>
    <li><svg width="14" height="14"><use href="#tick"/></svg>Long-Tail Keywords</li>
    <li><svg width="14" height="14"><use href="#tick"/></svg>Local SEO Benefits</li>
    <li><svg width="14" height="14"><use href="#tick"/></svg>Enhanced User Experience</li>
    <li><svg width="14" height="14"><use href="#tick"/></svg>Authority Building</li>
  </ul>
  <a class="btn btn-solid seo-cta" href="#">Sign Up For A Free Trial</a>
</section>

<section class="pricing">
  <h2 class="section-title pricing-title">Pricing</h2>
  <span class="bar"></span>
  <p class="abs pricing-copy">The platform can be used to sell unique accounts to multiple users. There must be a subscription plan and a 14-day free trial. The subscriptions are:</p>
  <div class="abs plans">
    <div class="plan"><h3>Base Plan</h3><p>1 blog post<br>(up to 2,000 words)<br>every month<span class="price">$9.99/<small>mo.</small></span></p></div>
    <div class="plan"><h3>Premium Plan</h3><p>1 blog post<br>(up to 2,000 words)<br>every week<span class="price">$14.99/<small>mo.</small></span></p></div>
    <div class="plan"><h3>Ultimate Plan</h3><p>1 blog post<br>(up to 3,000 words)<br>per day plus unlimited<br>manual posting<span class="price">$24.99/<small>mo.</small></span></p></div>
  </div>
  <a class="btn btn-light pricing-cta" href="#">Sign Up For A Free Trial</a>
</section>

<section class="reviews">
  <h2 class="section-title reviews-title">Let’s see our <span class="hl">Customer Say</span></h2>
  <a class="arrow arrow-prev" href="#" aria-label="Previous"><svg width="12" height="12" viewBox="0 0 12 12"><path d="M8 2L4 6l4 4" fill="none" stroke="#1E1E1E" stroke-width="1.6"/></svg></a>
  <article class="card" style="left:141px"><div class="stars">★★★★★</div><p>Lorem ipsum dolor sit amet, consectetur adipiscing elit. Proin suscipit metus tellus, at ultricies libero pulvinar sit amet.</p><div class="author"><span role="img" aria-label="Customer portrait" style="background:#8FA4B8"></span>Alex Johnson</div><div class="quote">”</div></article>
  <article class="card" style="left:455px"><div class="stars">★★★★★</div><p>Lorem ipsum dolor sit amet, consectetur adipiscing elit. Proin suscipit metus tellus, at ultricies libero pulvinar sit amet.</p><div class="author"><span role="img" aria-label="Customer portrait" style="background:#B9A58F"></span>Taylor Smith</div><div class="quote">”</div></article>
  <article class="card" style="left:769px"><div class="stars">★★★★★</div><p>Lorem ipsum dolor sit amet, consectetur adipiscing elit. Proin suscipit metus tellus, at ultricies libero pulvinar sit amet.</p><div class="author"><span role="img" aria-label="Customer portrait" style="background:#8C6A55"></span>Cameron Lee</div><div class="quote">”</div></article>
  <a class="arrow arrow-next" href="#" aria-label="Next"><svg width="12" height="12" viewBox="0 0 12 12"><path d="M4 2l4 4-4 4" fill="none" stroke="#FFFFFF" stroke-width="1.6"/></svg></a>
</section>

<footer class="site-footer">© 2024 PostNook. All Rights Reserved.</footer>
</body>
</html>
```